Ledgerwise Forge - WordPress Theme & Logo

Design a logo and Wordpress website design for Ledgerwise Forge. Ledgerwise Forge provides cryptocurrency development services to clients who need a team to create & continue developing a new cryptocurrency or who want to replace their current cryptocurrency development team. more details in the attached document.
Updates

Target Market(s)

Entrepreneurs who are building a business / platform that makes use of an underlying cryptocurrency.

Logo Text

LF or Ledgerwise Forge

Coding

Coded - Design and coding required

Font styles to use
Sans Serif

Requirements
Must have
• Professional logo, complete coded Wordpress theme for all pages, containing all specified links and buttons
Nice to have
• It would be nice if the buttons that are meant to integrate with Dealtrail contain the necessary code for that. I can provide any necessary Dealtrail details from my account.
Should not have
• Slow loading time

```html
<!DOCTYPE html>
<html lang="en">
<head>
<meta charset="utf-8">
<title>Ledgerwise Forge – Cryptocurrency Development</title>
<link rel="stylesheet" href="https://fonts.googleapis.com/css2?family=Fjalla+One&family=Montserrat:wght@400;500;600;700&family=Poppins:wght@500;600;700;800&display=swap">
<style>
:root{
  --teal:#2bc3b1;
  --teal-dark:#22a898;
  --navy:#0b1424;
  --navy-2:#111c30;
  --ink:#141414;
  --body:#2b2b2b;
  --muted:#555;
  --blush:#f4f0f1;
  --white:#fff;
  --footer:#1b1c1f;
  --rule:#e3e3e3;
}
*{box-sizing:border-box;margin:0;padding:0}
html,body{width:1200px;height:4124px;overflow:hidden}
body{position:relative;background:var(--white);font-family:'Montserrat',sans-serif;color:var(--body)}
.section-title{position:absolute;left:0;width:1200px;text-align:center;font-family:'Poppins',sans-serif;font-weight:700;font-size:23px;color:var(--ink);letter-spacing:-.2px;text-transform:uppercase}
.title-rule{position:absolute;left:568px;width:64px;height:3px;background:var(--teal)}
.btn{position:absolute;display:flex;align-items:center;justify-content:center;background:var(--teal);color:var(--white);font-family:'Montserrat',sans-serif;font-weight:700;text-decoration:none}

/* header + hero */
.hero{position:absolute;left:0;top:0;width:1200px;height:720px;background:linear-gradient(180deg,#070d18 0%,#0b1424 50%,#070d18 100%);overflow:hidden}
.hero-art{position:absolute;left:0;top:90px;width:1200px;height:630px;background:radial-gradient(ellipse 420px 300px at 380px 270px,rgba(60,110,150,.45),rgba(11,20,36,0) 100%),radial-gradient(ellipse 260px 420px at 1120px 300px,rgba(60,120,190,.35),rgba(11,20,36,0) 100%)}
.brand{position:absolute;left:34px;top:22px;font-family:'Fjalla One',sans-serif;font-size:29px;color:var(--teal)}
.nav{position:absolute;top:32px;left:308px;display:flex;gap:36px;font-size:14.5px;font-weight:500;color:var(--white)}
.nav a{color:var(--white);text-decoration:none}
.nav-cta{position:absolute;left:951px;top:21px;width:225px;height:43px;border:2px solid var(--white);color:var(--white);font-size:14px;font-weight:600;display:flex;align-items:center;justify-content:center;text-decoration:none}
.hero-head{position:absolute;left:654px;top:188px;font-family:'Poppins',sans-serif;font-weight:800;font-size:33px;line-height:54px;color:var(--white);text-transform:uppercase}
.hero-btn{width:301px;height:48px;font-size:17px}

/* welcome */
.lead{position:absolute;left:200px;width:800px;text-align:center;font-size:17px;line-height:29px;color:var(--body)}
.wave{position:absolute;left:0;top:960px;width:1200px;height:336px;background:radial-gradient(ellipse at 50% 40%,rgba(43,195,177,.35),rgba(43,195,177,.08) 55%,rgba(255,255,255,0) 75%)}

/* why cards */
.feature{position:absolute;top:1424px;width:294px;height:314px;background:var(--teal);color:var(--white);text-align:center}
.feature svg{position:absolute;left:107px;top:38px}
.feature h3{position:absolute;top:154px;width:100%;font-family:'Poppins',sans-serif;font-weight:700;font-size:20px}
.feature p{position:absolute;top:198px;left:50px;width:194px;font-size:16px;line-height:24px}

/* who we are */
.who{position:absolute;left:0;top:1795px;width:1200px;height:453px;background:radial-gradient(ellipse at 50% 30%,#1b2a40 0%,#0d1729 60%,#0a1322 100%)}
.who .section-title{top:73px;color:var(--white)}
.who p{position:absolute;left:230px;top:180px;width:740px;text-align:center;font-size:20.5px;line-height:35px;color:#e6ecf2;font-weight:400}

/* testimonials */
.testimonials{position:absolute;left:0;top:2248px;width:1200px;height:632px;background:var(--blush)}
.quote-card{position:absolute;top:184px;width:300px;height:392px;background:var(--white);text-align:center}
.avatar{position:absolute;left:105px;top:-48px;width:90px;height:90px;border-radius:50%;background:linear-gradient(160deg,#7a8793,#3b3f45)}
.quote-mark{position:absolute;top:78px;width:100%;font-family:'Poppins',sans-serif;font-size:40px;color:#b9b9b9;line-height:40px}
.quote-card p{position:absolute;top:128px;left:26px;width:248px;font-size:13.5px;line-height:20.5px;color:#333}
.quote-card h4{position:absolute;top:344px;width:100%;font-size:12px;font-weight:700;color:var(--ink);letter-spacing:.4px}

/* services */
.plexus{position:absolute;background:radial-gradient(circle,rgba(150,150,150,.18),rgba(255,255,255,0) 70%)}
.service{position:absolute;top:3176px;width:298px;height:482px;border:2px solid #3a3a3a;background:var(--white);text-align:center}
.service svg.icon{position:absolute;left:109px;top:34px}
.service h3{position:absolute;width:100%;font-family:'Poppins',sans-serif;font-weight:700;font-size:18px;color:var(--ink);line-height:26px}
.service .desc{position:absolute;left:40px;top:226px;width:218px;font-size:15px;line-height:23px;color:#333}
.checklist{position:absolute;left:26px;top:202px;width:248px;list-style:none;text-align:left}
.checklist li{position:relative;padding:0 0 12px 26px;margin-bottom:12px;border-bottom:1px solid var(--rule);font-size:13px;line-height:18px;color:#333}
.checklist li:last-child{border-bottom:0}
.checklist li svg{position:absolute;left:2px;top:4px}

/* footer */
.footer{position:absolute;left:0;top:3800px;width:1200px;height:324px;background:var(--footer);color:#ddd}
.footer .brand{left:131px;top:89px;font-size:35px}
.footer-links{position:absolute;top:58px;list-style:none;font-size:13px;line-height:24px;color:#ddd}
.news-title{position:absolute;left:714px;top:52px;font-family:'Poppins',sans-serif;font-weight:600;font-size:15px;color:var(--white)}
.news-input{position:absolute;left:717px;top:90px;width:217px;height:38px;background:var(--white);display:flex;align-items:center;padding-left:16px;gap:10px;font-size:12.5px;color:#333}
.news-btn{left:954px;top:90px;width:115px;height:38px;font-size:14px;letter-spacing:.3px}
.social{position:absolute;left:716px;top:154px;display:flex;gap:21px}
.social span{width:16px;height:16px;border-radius:50%;background:#e8e8e8}
.footer-rule{position:absolute;left:131px;top:221px;width:938px;height:1px;background:#3b3c40}
.copyright{position:absolute;left:0;top:264px;width:1200px;text-align:center;font-size:13px;color:#ddd}
</style>
</head>
<body>

<header class="hero">
  <div class="hero-art" role="img" aria-label="Dark digital currency artwork with glowing code"></div>
  <div class="brand">Ledgerwise Forge</div>
  <nav class="nav">
    <a href="#">Services</a><a href="#">Ledgerwise Forge Method</a><a href="#">Testimonials</a><a href="#">Blog</a><a href="#">About Us</a>
  </nav>
  <a class="nav-cta" href="#">Schedule Free Consultation</a>
  <h1 class="hero-head">Your own<br>cryptocurrency.<br>Secure, easy to use, and<br>built by an expert team.</h1>
  <a class="btn hero-btn" style="left:661px;top:437px" href="#">Schedule Free Consultation</a>
  <a class="btn hero-btn" style="left:661px;top:512px" href="#">Download a free PDF</a>
</header>

<h2 class="section-title" style="top:773px">Welcome to Ledgerwise Forge</h2>
<div class="title-rule" style="top:822px"></div>
<p class="lead" style="top:853px">Ledgerwise Forge adds professionalism to cryptocurrency development. Our done-for-you service covers everything from development and IT operations to ongoing support. You have access to a full team, for less than the typical cost of a single developer</p>

<div class="wave" role="img" aria-label="Flowing teal line wave decoration"></div>

<h2 class="section-title" style="top:1322px">Why choose Ledgerwise Forge</h2>

<div class="feature" style="left:131px">
  <svg width="80" height="80" viewBox="0 0 80 80" fill="none" stroke="#fff" stroke-width="3"><polygon points="16,30 28,16 52,16 64,30 40,66"/><line x1="16" y1="30" x2="64" y2="30"/><line x1="40" y1="4" x2="40" y2="10"/></svg>
  <h3>Value</h3>
  <p>A team of experts, regular updates, and fixed costs</p>
</div>
<div class="feature" style="left:453px">
  <svg width="80" height="80" viewBox="0 0 80 80" fill="none" stroke="#fff" stroke-width="3"><path d="M20 40V32a20 20 0 0 1 40 0v8"/><rect x="14" y="38" width="10" height="18" rx="4"/><rect x="56" y="38" width="10" height="18" rx="4"/><path d="M61 56q0 10-14 10h-5"/></svg>
  <h3>Support</h3>
  <p>Receive advice and other services, beyond development.</p>
</div>
<div class="feature" style="left:776px">
  <svg width="80" height="80" viewBox="0 0 80 80" fill="none" stroke="#fff" stroke-width="3"><path d="M8 38l14-14 12 6 12-6 14 4 12 10-22 22-10-8-10 6z"/><line x1="40" y1="6" x2="40" y2="14"/><line x1="26" y1="10" x2="30" y2="16"/><line x1="54" y1="10" x2="50" y2="16"/></svg>
  <h3>Commitment</h3>
  <p>Enjoy regular updates and new features.</p>
</div>

<section class="who">
  <h2 class="section-title">Who we are</h2>
  <p>In addition to creating and enhancing cryptocurrencies for clients, the Ledgerwise Forge team has been running the Quillon cryptocurrency since 2017. We prefer long-term relationships, enabling us to deliver the very highest quality and giving you peace of mind that you’ve got a professional and trustworthy team at your side.</p>
</section>

<section class="testimonials">
  <h2 class="section-title" style="top:43px">Client testimonials</h2>
  <div class="title-rule" style="top:91px"></div>
  <div class="quote-card" style="left:126px">
    <div class="avatar" role="img" aria-label="Client portrait"></div>
    <div class="quote-mark">“</div>
    <p>Sed ut perspiciatis unde omnis iste natus error sit voluptatem accus antium doloremque laud antium, totam rem aperiam, eaque ipsa quae ab illo inventore veritatis et quasi architecto beatae vitae dicta sunt expli cabo. Nemo enim ipsam volup tatem quia volu ptas sit aspernatur.</p>
    <h4>MARCUS</h4>
  </div>
  <div class="quote-card" style="left:450px">
    <div class="avatar" role="img" aria-label="Client portrait"></div>
    <div class="quote-mark">“</div>
    <p>Sed ut perspiciatis unde omnis iste natus error sit voluptatem accus antium doloremque laud antium, totam rem aperiam, eaque ipsa quae ab illo inventore veritatis et quasi architecto beatae vitae dicta sunt expli cabo. Nemo enim ipsam volup tatem quia volu ptas sit aspernatur.</p>
    <h4>MARCUS</h4>
  </div>
  <div class="quote-card" style="left:774px">
    <div class="avatar" role="img" aria-label="Client portrait"></div>
    <div class="quote-mark">“</div>
    <p>Sed ut perspiciatis unde omnis iste natus error sit voluptatem accus antium doloremque laud antium, totam rem aperiam, eaque ipsa quae ab illo inventore veritatis et quasi architecto beatae vitae dicta sunt expli cabo. Nemo enim ipsam volup tatem quia volu ptas sit aspernatur.</p>
    <h4>MARCUS</h4>
  </div>
</section>

<div class="plexus" style="left:960px;top:2880px;width:240px;height:300px" role="img" aria-label="Faint network mesh decoration"></div>
<div class="plexus" style="left:0;top:3500px;width:240px;height:300px" role="img" aria-label="Faint network mesh decoration"></div>
<div class="plexus" style="left:1040px;top:3620px;width:160px;height:180px" role="img" aria-label="Faint network mesh decoration"></div>

<h2 class="section-title" style="top:2935px">Services</h2>
<p class="lead" style="top:3018px;left:215px;width:770px;font-size:14.5px;line-height:22.5px">Ledgerwise Forge provides a complete service that handles the development, IT operations and support for your cryptocurrency. Cryptocurrency development can be difficult and complex, and a quality development team is hard to find and expensive. Ledgerwise Forge has an experienced team that has helped several clients launch and enhance their cryptocurrencies, including successfully running the Quillon cryptocurrency since 2017, and writing a next-generation cryptocurrency from scratch.</p>

<div class="service" style="left:131px">
  <svg class="icon" width="80" height="80" viewBox="0 0 80 80" fill="none" stroke="#2bc3b1" stroke-width="2.5"><rect x="8" y="8" width="16" height="16"/><rect x="32" y="8" width="16" height="16"/><rect x="56" y="8" width="16" height="16"/><rect x="8" y="32" width="16" height="16"/><rect x="32" y="32" width="16" height="16"/><rect x="56" y="32" width="16" height="16"/><rect x="20" y="56" width="16" height="16"/><rect x="44" y="56" width="16" height="16"/></svg>
  <h3 style="top:148px">Blockchain<br>Creation &amp; Launch</h3>
  <p class="desc">Base fixed price for cryptocurrency development &amp; launch--would be customizable based on client requirements</p>
</div>

<div class="service" style="left:453px">
  <svg class="icon" width="80" height="80" viewBox="0 0 80 80" fill="none" stroke="#2bc3b1" stroke-width="2.5"><rect x="22" y="16" width="36" height="30" rx="3"/><line x1="22" y1="26" x2="58" y2="26"/><path d="M8 60h16l14 6 22-10"/><line x1="40" y1="6" x2="40" y2="12"/></svg>
  <h3 style="top:157px">Basic offering</h3>
  <ul class="checklist">
    <li><svg width="12" height="10" viewBox="0 0 12 10"><polyline points="1,5 4.5,8.5 11,1" fill="none" stroke="#2bc3b1" stroke-width="2"/></svg>Lower cost per month</li>
    <li><svg width="12" height="10" viewBox="0 0 12 10"><polyline points="1,5 4.5,8.5 11,1" fill="none" stroke="#2bc3b1" stroke-width="2"/></svg>Slower release schedule<br>(about every 3 months)</li>
    <li><svg width="12" height="10" viewBox="0 0 12 10"><polyline points="1,5 4.5,8.5 11,1" fill="none" stroke="#2bc3b1" stroke-width="2"/></svg>Client assists with testing<br>new releases</li>
    <li><svg width="12" height="10" viewBox="0 0 12 10"><polyline points="1,5 4.5,8.5 11,1" fill="none" stroke="#2bc3b1" stroke-width="2"/></svg>Less input into future roadmap<br>/features</li>
    <li><svg width="12" height="10" viewBox="0 0 12 10"><polyline points="1,5 4.5,8.5 11,1" fill="none" stroke="#2bc3b1" stroke-width="2"/></svg>Limited support hours/priority<br>(always available for emergencies)</li>
  </ul>
</div>

<div class="service" style="left:774px">
  <svg class="icon" width="80" height="80" viewBox="0 0 80 80" fill="none" stroke="#2bc3b1" stroke-width="2.5"><circle cx="40" cy="40" r="34"/><circle cx="40" cy="40" r="26"/></svg>
  <h3 style="top:157px">Full service offering</h3>
  <ul class="checklist">
    <li><svg width="12" height="10" viewBox="0 0 12 10"><polyline points="1,5 4.5,8.5 11,1" fill="none" stroke="#2bc3b1" stroke-width="2"/></svg>Mid-range cost per month</li>
    <li><svg width="12" height="10" viewBox="0 0 12 10"><polyline points="1,5 4.5,8.5 11,1" fill="none" stroke="#2bc3b1" stroke-width="2"/></svg>Releases every 1.5 - 2 months</li>
    <li><svg width="12" height="10" viewBox="0 0 12 10"><polyline points="1,5 4.5,8.5 11,1" fill="none" stroke="#2bc3b1" stroke-width="2"/></svg>Client can help request/prioritize<br>new features</li>
    <li><svg width="12" height="10" viewBox="0 0 12 10"><polyline points="1,5 4.5,8.5 11,1" fill="none" stroke="#2bc3b1" stroke-width="2"/></svg>Full testing by my team prior<br>to release</li>
    <li><svg width="12" height="10" viewBox="0 0 12 10"><polyline points="1,5 4.5,8.5 11,1" fill="none" stroke="#2bc3b1" stroke-width="2"/></svg>Priority support during normal business hours, always available for emergencies</li>
  </ul>
</div>

<a class="btn" style="left:478px;top:3701px;width:244px;height:45px;font-size:14px" href="#">Schedule Free Consultation</a>

<footer class="footer">
  <div class="brand">Ledgerwise Forge</div>
  <ul class="footer-links" style="left:456px"><li>Home</li><li>About</li><li>Feature</li><li>Pricing</li><li>Contact</li></ul>
  <ul class="footer-links" style="left:570px"><li>Blog</li><li>Search</li><li>T $ Cs</li><li>Privacy</li><li>Contact Us</li></ul>
  <div class="news-title">Get our Newsletter</div>
  <div class="news-input"><svg width="12" height="10" viewBox="0 0 12 10"><rect x="0.5" y="0.5" width="11" height="9" fill="#333"/><polyline points="1,1 6,6 11,1" fill="none" stroke="#fff" stroke-width="1.2"/></svg>Enter Your email</div>
  <a class="btn news-btn" href="#">SUBSCRIBE</a>
  <div class="social"><span></span><span></span><span></span><span></span><span></span></div>
  <div class="footer-rule"></div>
  <div class="copyright">Copyright © 2021 All Rights Reserved</div>
</footer>

</body>
</html>
```